Help Give House Painter “Fresh” Website Makeover!

A residential and commercial painting company based in Albuquerque, NM, USA needs a fresh, new, fun, and playful--yet, simple, elegant and professional--website made.

Here is a link to their existing site:

http://corvelcoatings.example/

We want to keep a similar site structure., So the navigation layout will stay the same. However, the video is too small, is too far over in the sidebar, and the overall design is amateur at best. We want something bright, colorful and bold!

We will need a space for the Video above the fold, and there needs to be space in the design for Testimonials, Specials and Images. It’s also very important to have the Pellham Roster awards that you see on his current website.

Please also include somewhere in the Design icons for YouTube, Facebook, Google+ and LinkedIn.

Here are some examples to look at to get your creative juices flowing!

http://brightloombrush.example/

http://www.tkvr.example/

http://www.marblow-tennick.example/

http://www.quarrypages.example/painting-company-niche-website/

http://www.brisklayoutdepot.example/website-templates/painting-company-website-template-53817.html

We have accounts at both lumavault.example and pixaroo.example. If you use placeholder images from there, that's fine. We can buy the images when and if your design is selected.

Target Market(s)

The audience is the average middle class homeowner to higher upper class. This should appeal to families, couples, and singles who own a home.

Industry/Entity Type

Residential

Font styles to use
Sans Serif

Requirements
Must have
• - - Lots of color! It's a site about painting homes. People like a variety of colors. Bring out your inner artist, and get bold with your colors!

- - A video place holder. As you can see, there is a video on the existing site, but it's small and hidden. Make it big and put it top left, or in the center.

- -Detailed and organized PSD structure. We're going to turn your design into a website, and to make that work soothly, we ask that you organize you PSD well: name your layers, keep things separated, group and ungroup as necessary, etc.

- A sidebar that goes down the right side of an interior page. We need a homepage, and also one [1] interior page template. We don't need you to make a design for each page. Just the homepage, followed by a simple interior page design that requires only the header/navigation, and a sidebar down the right side.
Should not have
• - Coding. This is a design project only.

```html
<!DOCTYPE html>
<html lang="en">
<head>
<meta charset="utf-8">
<title>Corvel Coatings – Residential &amp; Commercial Painting</title>
<link rel="stylesheet" href="https://fonts.googleapis.com/css2?family=Lato:ital,wght@0,400;0,700;0,900;1,400;1,700&family=Oswald:wght@400;500&display=swap">
<style>
:root{
  --blue:#0b4ea2;
  --nav-blue:#1a7fd0;
  --red:#e31d2b;
  --red-deep:#c9252f;
  --yellow:#f7a823;
  --gold:#f5b335;
  --orange:#f58220;
  --teal:#2a87c0;
  --green:#3b9c1a;
  --navy:#0d3d8a;
  --mustard:#c98a12;
  --grey-bg:#f2f2f2;
  --badge:#d8d8d8;
  --text:#333;
  --white:#fff;
}
*{box-sizing:border-box;margin:0;padding:0}
html,body{width:768px;height:1200px;overflow:hidden}
body{position:relative;background:var(--white);font-family:'Lato',sans-serif;color:var(--text)}
.abs{position:absolute}

/* header */
.site-header{position:absolute;left:0;top:0;width:768px;height:78px;background:var(--white)}
.brand-dot{left:88px;top:24px;width:26px;height:26px;border-radius:50%;background:var(--blue)}
.brand-name{left:124px;top:27px;font:900 22px/1 'Lato',sans-serif;color:var(--blue);letter-spacing:.5px}
.award{top:8px;width:100px;text-align:center;font:700 7.5px/1 'Lato',sans-serif;color:#222}
.award-shape{display:block;margin:0 auto 8px;width:36px;height:44px;background:var(--badge);border-radius:3px}
.header-phone{left:574px;top:33px;font:400 16px/1 'Lato',sans-serif;color:var(--red);display:flex;align-items:center;gap:6px}

/* nav */
.main-nav{left:0;top:78px;width:768px;height:29px;background:linear-gradient(#2a94e2,#0b62b4);display:flex;padding-left:83px}
.main-nav a{color:var(--white);text-decoration:none;font:700 9.3px/29px 'Lato',sans-serif;margin-right:17px}
.main-nav a.active{border-bottom:1px solid var(--white);line-height:22px;height:24px;margin-top:3px}

/* hero */
.hero-bg{left:0;top:107px;width:768px;height:303px;background:linear-gradient(90deg,#d9d2c9 0%,#e9e3dc 10%,#f09b3c 89%,#e98a2e 100%)}
.video{left:84px;top:107px;width:408px;height:231px}
.video-frame{left:0;top:0;width:408px;height:213px;background:linear-gradient(90deg,#e0701f 0%,#d86a1c 46%,#d9d9d9 50%,#eeeeee 100%)}
.video-title{left:0;top:30px;width:206px;text-align:center;font:900 14px/1 'Lato',sans-serif;color:var(--blue)}
.video-sub{left:0;top:51px;width:206px;text-align:center;font:500 17px/1.12 'Oswald',sans-serif;color:var(--white);text-transform:uppercase}
.play{left:188px;top:99px;width:32px;height:21px;border-radius:5px;background:#e52620}
.video-controls{left:0;top:213px;width:408px;height:18px;background:linear-gradient(#3c3c3c,#111)}
.ctrl-btn{top:4px;width:14px;height:10px;border-radius:2px;background:#3b6fb0}
.ctrl-track{left:32px;top:7px;width:120px;height:4px;border-radius:2px;background:#ccc}
.ctrl-time{left:158px;top:5px;font:400 6px/1 'Lato',sans-serif;color:#ddd}
.hero-call{left:84px;top:338px;width:408px;height:72px;background:var(--blue);text-align:center;color:var(--white);font-family:'Oswald',sans-serif}
.hero-call .l1{margin-top:8px;font-size:12.5px}
.hero-call .l2{margin-top:2px;font-size:15.5px}
.hero-call .l2 span{color:var(--gold)}
.hero-call .l3{margin-top:2px;font-size:12.5px}

/* estimate form */
.estimate{left:492px;top:107px;width:192px;height:303px;background:var(--red-deep)}
.estimate-head{left:0;top:0;width:192px;height:38px;background:linear-gradient(#f9c448,#e89a16);font:500 13.5px/34px 'Oswald',sans-serif;color:var(--white);text-align:center}
.estimate h3{position:absolute;left:0;top:57px;width:192px;text-align:center;font:700 11.5px/1 'Lato',sans-serif;color:var(--white)}
.estimate p{position:absolute;left:14px;top:73px;width:164px;text-align:center;font:400 7.8px/1.3 'Lato',sans-serif;color:var(--white)}
.field{left:11px;width:170px;height:16px;background:var(--white);border-radius:3px;font:400 7.5px/16px 'Lato',sans-serif;color:#333;padding-left:6px}
.field.area{height:36px;line-height:1;padding-top:5px}
.captcha-label{left:11px;top:232px;font:400 7.5px/1 'Lato',sans-serif;color:var(--white)}
.submit{left:11px;top:267px;width:84px;height:21px;border-radius:3px;background:linear-gradient(#fbc246,#ec9a18);font:700 10px/21px 'Lato',sans-serif;color:var(--white);text-align:center}

/* main content */
.content-bg{left:0;top:410px;width:768px;height:575px;background:var(--grey-bg)}
.sidebar-bg{left:492px;top:410px;width:192px;height:575px;background:#fafafa}
.welcome-title{left:84px;top:434px;font:700 12.5px/1 'Lato',sans-serif;color:#222}
.welcome-title span{color:var(--blue)}
.welcome-text{left:84px;top:462px;width:396px;font:400 8.6px/1.55 'Lato',sans-serif;color:#333}
.welcome-text p+p{margin-top:6px}
.read-more{left:84px;top:601px;width:61px;height:21px;border-radius:3px;background:var(--red);font:700 8.5px/21px 'Lato',sans-serif;color:var(--white);text-align:center;box-shadow:0 2px 0 #a6121c}

.service{width:126px;height:116px}
.service .band{position:absolute;left:0;top:0;width:126px;height:62px;border-radius:4px 4px 0 0}
.service .name{position:absolute;left:0;top:44px;width:126px;text-align:center;font:700 8.3px/1 'Lato',sans-serif;color:var(--white)}
.service .desc{position:absolute;left:0;top:62px;width:126px;height:33px;background:var(--gold);text-align:center;font:700 7px/1.35 'Lato',sans-serif;color:#333;padding:5px 6px 0}
.service .more{position:absolute;left:0;top:95px;width:126px;height:21px;border-radius:0 0 4px 4px;text-align:center;font:700 7.5px/21px 'Lato',sans-serif;color:var(--white);text-decoration:underline}
.service .photo{position:absolute;left:24px;top:-38px;width:78px;height:78px;border-radius:50%;border:4px solid var(--white);box-shadow:0 1px 3px rgba(0,0,0,.25)}

/* sidebar */
.side-title{left:504px;top:434px;font:700 12.5px/1 'Lato',sans-serif;color:var(--blue)}
.side-title span{color:var(--red)}
.side-rule{left:504px;top:452px;width:134px;height:1px;background:#e5b3b3}
.quote{left:504px;width:169px;background:#e6e6e6;border-radius:4px;padding:7px 10px 8px 10px;font:italic 400 7.8px/1.4 'Lato',sans-serif;color:#333}
.quote::before{content:"\201C";font:700 18px/0 Georgia,serif;color:#bbb;margin-right:3px;vertical-align:-6px}
.avatar{width:48px;height:48px;border-radius:50%;border:3px solid var(--white);background:linear-gradient(#6b7f98,#2b3b52);box-shadow:0 1px 3px rgba(0,0,0,.3)}
.client{font:700 8px/1 'Lato',sans-serif;color:var(--blue)}
.stars{color:var(--yellow);font-size:11px;letter-spacing:1px}
.specials{left:503px;top:780px;width:170px;height:187px;border:1px solid var(--red);background:var(--white)}
.specials-art{left:0;top:30px;width:168px;height:120px;background:linear-gradient(90deg,#d4151f 0%,#e3202a 70%,#f7f7f7 80%,#ffffff 100%)}
.specials-text{left:10px;top:75px;width:105px;text-align:center;font:italic 700 14px/1.4 'Lato',sans-serif;color:var(--white);text-decoration:underline}

/* footer */
.site-footer{left:0;top:985px;width:768px;height:215px;background:var(--blue)}
.foot-nav{left:0;top:1003px;width:768px;text-align:center;font:700 8px/1 'Lato',sans-serif;color:var(--white)}
.foot-nav span{margin:0 2px}
.rule{height:1px;background:rgba(255,255,255,.25)}
.foot-h{font:700 10.5px/1 'Lato',sans-serif;color:var(--white)}
.news-input{left:177px;top:1055px;width:200px;height:23px;background:var(--white);font:400 7px/23px 'Lato',sans-serif;color:#999;padding-left:9px}
.news-submit{left:381px;top:1055px;width:54px;height:23px;background:var(--red);font:700 9px/23px 'Lato',sans-serif;color:var(--white);text-align:center}
.vdiv{width:1px;background:rgba(255,255,255,.25)}
.social{top:1055px;width:20px;height:20px;border-radius:50%}
.foot-info{font:400 8px/1.45 'Lato',sans-serif;color:var(--white)}
.trust{left:481px;top:1106px;width:110px;height:46px;background:var(--white);border-radius:4px}
.trust-shape{left:17px;top:8px;width:76px;height:30px;border-radius:3px;background:#1c5d7a}
.copyright{left:0;top:1177px;width:768px;text-align:center;font:700 8px/1 'Lato',sans-serif;color:var(--white)}
</style>
</head>
<body>

<header class="site-header">
  <div class="abs brand-dot"></div>
  <div class="abs brand-name">CORVEL COATINGS</div>
  <div class="abs award" style="left:364px"><span class="award-shape" role="img" aria-label="Pellham Roster award badge"></span>EXTERIOR PAINTING</div>
  <div class="abs award" style="left:451px"><span class="award-shape" role="img" aria-label="Pellham Roster award badge"></span>INTERIOR PAINTING</div>
  <div class="abs header-phone">
    <svg width="16" height="16" viewBox="0 0 16 16"><circle cx="8" cy="8" r="7" fill="none" stroke="#0b4ea2" stroke-width="1.4"/><path d="M5.3 4.5l1.4-.2.8 2-.9.7a5 5 0 0 0 2.3 2.3l.7-.9 2 .8-.2 1.4c-3.3.3-6.4-2.8-6.1-6.1z" fill="#0b4ea2"/></svg>
    555 010 2840
  </div>
</header>

<nav class="abs main-nav">
  <a class="active" href="#">HOME</a><a href="#">ABOUT US</a><a href="#">RESIDENTIAL PAINTING</a><a href="#">COMMERCIAL PAINTING</a><a href="#">FAQ</a><a href="#">SPECIALS</a><a href="#">BLOG</a><a href="#">TESTIMONIALS</a><a href="#">CONTACT US</a>
</nav>

<section class="hero">
  <div class="abs hero-bg" role="img" aria-label="Painted room interior with orange wall and wooden floor"></div>
  <div class="abs video">
    <div class="abs video-frame" role="img" aria-label="Video still of a bedroom half painted orange, half white"></div>
    <div class="abs video-title">CORVEL COATINGS</div>
    <div class="abs video-sub">Residential &amp; Commercial<br>Painting Company</div>
    <div class="abs play"><svg width="32" height="21" viewBox="0 0 32 21"><path d="M13 6l7 4.5-7 4.5z" fill="#fff"/></svg></div>
    <div class="abs video-controls">
      <div class="abs ctrl-btn" style="left:6px"></div>
      <div class="abs ctrl-track"></div>
      <div class="abs ctrl-time">147 / 12:35</div>
      <div class="abs ctrl-btn" style="left:350px"></div>
      <div class="abs ctrl-btn" style="left:370px"></div>
      <div class="abs ctrl-btn" style="left:390px"></div>
    </div>
  </div>
  <div class="abs hero-call">
    <div class="l1">Need Painting In The Albuquerque Area?</div>
    <div class="l2">Call Wade Today For Your FREE Painting Estimate! <span>555-0166</span></div>
    <div class="l3">Licensed - Bonded - Insured</div>
  </div>

  <form class="abs estimate">
    <div class="abs estimate-head">SCHEDULE FREE ESTIMATE</div>
    <h3>How to Schedule an Estimae</h3>
    <p>Requesting an estimate online is very simple and easy. Fill out the Form below and we will send you a rough quote to your email. We may also call you if we have any more questions.</p>
    <div class="abs field" style="top:125px">Name:</div>
    <div class="abs field" style="top:147px">Email:</div>
    <div class="abs field" style="top:169px">Phone:</div>
    <div class="abs field area" style="top:190px">Decribe what needs to be done.</div>
    <div class="abs captcha-label">Please type the following</div>
    <div class="abs field" style="top:243px">ac2gH</div>
    <div class="abs submit">Submit Now</div>
  </form>
</section>

<main>
  <div class="abs content-bg"></div>
  <div class="abs sidebar-bg"></div>

  <h2 class="abs welcome-title">WELCOME TO <span>CORVEL COATINGS</span></h2>
  <div class="abs welcome-text">
    <p>Corvel Coatings does jobs as small as a bathroom up to large commercial projects right here in Albuquerque and Rio Rancho. Extensive as an entire apartment exterior, to a kitchen and all home interior, no job is too big or too small for Corvel Coatings of Albuquerque. Corvel Coatings is staffed with the best painters for the highest quality paint jobs. Corvel Coatings is not a community's average house painter staffing company, but this painting company is staffed with professional painters that pride themselves on successfully completing every job.</p>
    <p>Wade Lorimer, owner of Corvel Coatings, Inc., started painting in 1975 during high school. He continued painting through college where he earned a Bachelor of Science degree from Prairie State University in 1984. Wade opened his first painting company in 1984.</p>
  </div>
  <div class="abs read-more">Read More</div>

  <div class="abs service" style="left:84px;top:679px">
    <div class="band" style="background:var(--orange)"></div>
    <div class="photo" role="img" aria-label="Roller painting a yellow wall" style="background:radial-gradient(#f6d04a,#d9a21a)"></div>
    <div class="name">COMMERCIAL PAINTING</div>
    <div class="desc">Lorem ipsum dolor sit a consecte adipiscing Lorem ipsum...</div>
    <div class="more" style="background:var(--orange)">Read more</div>
  </div>
  <div class="abs service" style="left:218px;top:679px">
    <div class="band" style="background:var(--teal)"></div>
    <div class="photo" role="img" aria-label="Couple painting a room" style="background:radial-gradient(#cfe3ee,#7fa8b8)"></div>
    <div class="name">RESIDENTIAL PAINTING</div>
    <div class="desc">Lorem ipsum dolor sit a consecte adipiscing Lorem ipsum...</div>
    <div class="more" style="background:var(--teal)">Read more</div>
  </div>
  <div class="abs service" style="left:354px;top:679px">
    <div class="band" style="background:var(--green)"></div>
    <div class="photo" role="img" aria-label="Stucco building facade" style="background:radial-gradient(#d9955a,#8a5a33)"></div>
    <div class="name">STUCCO COATINGS</div>
    <div class="desc">Lorem ipsum dolor sit a consecte adipiscing Lorem ipsum...</div>
    <div class="more" style="background:var(--green)">Read more</div>
  </div>

  <div class="abs service" style="left:84px;top:851px">
    <div class="band" style="background:var(--navy)"></div>
    <div class="photo" role="img" aria-label="Wooden kitchen cabinets" style="background:radial-gradient(#a0683a,#5a3518)"></div>
    <div class="name">CABINETS</div>
    <div class="desc">Lorem ipsum dolor sit a consecte adipiscing Lorem ipsum...</div>
    <div class="more" style="background:var(--navy)">Read more</div>
  </div>
  <div class="abs service" style="left:218px;top:851px">
    <div class="band" style="background:var(--red)"></div>
    <div class="photo" role="img" aria-label="Bright painted interior" style="background:radial-gradient(#e8e2d8,#9e8f7c)"></div>
    <div class="name">INTERIOR/ EXTERIOR</div>
    <div class="desc">Lorem ipsum dolor sit a consecte adipiscing Lorem ipsum...</div>
    <div class="more" style="background:var(--red)">Read more</div>
  </div>
  <div class="abs service" style="left:354px;top:851px">
    <div class="band" style="background:var(--mustard)"></div>
    <div class="photo" role="img" aria-label="Roller on blue drywall texture" style="background:radial-gradient(#4f98e0,#1c5ca8)"></div>
    <div class="name">DRY WALL TEXTURE REPAIR</div>
    <div class="desc">Lorem ipsum dolor sit a consecte adipiscing Lorem ipsum...</div>
    <div class="more" style="background:var(--mustard)">Read more</div>
  </div>

  <aside>
    <h2 class="abs side-title">CLIENT <span>TESTIMONIALS</span></h2>
    <div class="abs side-rule"></div>

    <blockquote class="abs quote" style="top:465px;height:100px">I chose Corvel Coatings to completely repaint the interior of my new home. The home was vacant when the painting was completed. My husband and I were delighted that the work was done on schedule and the quality of the painting was very good (nice clean li(...)</blockquote>
    <div class="abs avatar" style="left:520px;top:555px" role="img" aria-label="Client portrait"></div>
    <div class="abs client" style="left:580px;top:581px">Renata Osk</div>
    <div class="abs stars" style="left:579px;top:592px">★★★★★</div>

    <blockquote class="abs quote" style="top:618px;height:90px">Excellent work and an excellent price. We had a small area of stucco that fell off about a year after being painted. Wade and his team came in and patched and painted it without a hassle. Highly recommended</blockquote>
    <div class="abs avatar" style="left:520px;top:708px" role="img" aria-label="Client portrait"></div>
    <div class="abs client" style="left:580px;top:734px">Tomas Brell</div>
    <div class="abs stars" style="left:579px;top:745px">★★★★★</div>

    <div class="abs specials">
      <div class="abs specials-art" role="img" aria-label="Red paint roller stroke"></div>
      <div class="abs specials-text">Check Out<br>Our Specials!</div>
    </div>
  </aside>
</main>

<footer class="abs site-footer"></footer>
<div class="abs foot-nav">HOME <span>•</span> ABOUT US <span>•</span> RESIDENTIAL PAINTING <span>•</span> COMMERCIAL PAINTING <span>•</span> FAQ <span>•</span> SPECIALS <span>•</span> BLOG <span>•</span> TESTIMONIALS <span>•</span> CONTACT US</div>
<div class="abs rule" style="left:100px;top:1023px;width:568px"></div>

<div class="abs foot-h" style="left:177px;top:1035px">Sign up for Newsletter</div>
<div class="abs news-input">Enter Your Email</div>
<div class="abs news-submit">SUBMIT</div>
<div class="abs vdiv" style="left:458px;top:1033px;height:50px"></div>
<div class="abs foot-h" style="left:482px;top:1035px">Follow Us On</div>
<div class="abs social" style="left:482px;background:#2e6f8a"></div>
<div class="abs social" style="left:508px;background:#3b8fc0"></div>
<div class="abs social" style="left:534px;background:#23607a"></div>
<div class="abs social" style="left:560px;background:#b5413a"></div>

<svg class="abs" style="left:175px;top:1112px" width="10" height="14" viewBox="0 0 10 14"><path d="M5 0a5 5 0 0 1 5 5c0 3.5-5 9-5 9S0 8.5 0 5a5 5 0 0 1 5-5z" fill="#fff"/><circle cx="5" cy="5" r="1.8" fill="#0b4ea2"/></svg>
<div class="abs foot-info" style="left:193px;top:1111px">Corvel Coatings Inc.<br>4120 Larkspur Avenue Northeast,<br>Albuquerque, NM 87100</div>
<svg class="abs" style="left:357px;top:1111px" width="11" height="11" viewBox="0 0 11 11"><path d="M1 1.5l2.3-.5 1.2 2.6-1.3 1a6 6 0 0 0 3.2 3.2l1-1.3L10 7.7 9.5 10C4.8 10.3.7 6.2 1 1.5z" fill="#fff"/></svg>
<div class="abs foot-info" style="left:373px;top:1111px">555-013-2788</div>
<svg class="abs" style="left:323px;top:1137px" width="13" height="9" viewBox="0 0 13 9"><rect width="13" height="9" fill="#fff"/><path d="M0 0l6.5 5L13 0" fill="none" stroke="#0b4ea2" stroke-width="1"/></svg>
<div class="abs foot-info" style="left:341px;top:1134px">info@corvelcoatings.example</div>
<div class="abs vdiv" style="left:458px;top:1106px;height:46px"></div>
<div class="abs trust" role="img" aria-label="Accreditation badge"><div class="abs trust-shape"></div></div>
<div class="abs rule" style="left:177px;top:1165px;width:414px"></div>
<div class="abs copyright">© 2015 CORVEL COATINGS. All Rights Reserved.</div>

</body>
</html>
```